Ridge Lass Crew (Flyer)

I want a flyer to advertise my service.
Details below, and logo's to use are attached.

A girls only after school program, 11-14yrs, as OSHC is no longer avail, dedicated to coaching & mentoring our girls into strong, independent young women.

The Brainchild of Rebecca Folwin, Ridge Lass Crew was created to address the growing demand for after school/school holiday supervision for kids moving from primary into high school, when OSHC ceases to exist.
With over 12 years experience mentoring and coaching young women in the corporate world, Bec decided to leave her role as a Director with Tarrant Trust, and follow her passion.
Bec, along with her sister Lorraine, who has over 10 years experience in local communities as a Youth Worker, and is also a qualified Enrolled Nurse, embarked on building a program designed to keep parents happy (by knowing their girls are safe) and dedicated to coaching and mentoring our girls into strong, independent young women.
Open every afternoon and during school holidays, we look to offer;
- Daily meditation
- Healthy snacks
- Dedicated homework time
- Organised group activity, led by qualified instructors (yoga, fitness class, soccer etc)
- Regular guests speakers, addressing issues/concerns for young people today
- SOCIAL MEDIA FREE ZONE

Located 87 Pelham Pde, Baulkham Hills (across from Crestmoor Day Clinic)
Open 3-6pm Monday to Friday

Facebook page: http://fb.example/ridgelasscrew
Email: info@ridgelasscrew.example.au
Mobile: 0455817396

Target Market(s)

Parents of teenage girls, teenage girls 11-14 years

Industry/Entity Type

School

Font styles to use
Sans Serif

Colors
b768aa
e667a6

Requirements
Must have
• What progam is - see brief
• Who runs it
Should not have
• Not be too busy, not overly mature images

```html
<!DOCTYPE html>
<html lang="en">
<head>
<meta charset="utf-8">
<title>Ridge Lass Crew – After School Program Flyer</title>
<link rel="stylesheet" href="https://fonts.googleapis.com/css2?family=Bebas+Neue&family=Oswald:wght@300;400;600&display=swap">
<style>
  :root{
    --purple:#b864ee;
    --purple-deep:#4a1f63;
    --ink:#2f1540;
    --pink-soft:#f3c6ef;
    --white:#ffffff;
    --desk-light:#f4f2f3;
    --desk-mid:#dcd8dc;
  }
  html,body{margin:0;padding:0;overflow:hidden;background:#fff;}
  .flyer{
    position:relative;width:861px;height:1200px;overflow:hidden;
    font-family:"Bebas Neue","Oswald",sans-serif;color:var(--ink);
  }
  .desk-photo{
    position:absolute;inset:0;
    background:linear-gradient(160deg,var(--desk-light) 0%,#ebe8ea 45%,var(--desk-mid) 100%);
  }
  .shapes{position:absolute;inset:0;}
  .logo-box{
    position:absolute;left:30px;top:54px;width:336px;height:384px;background:var(--white);
    display:flex;align-items:center;justify-content:center;gap:12px;
  }
  .logo-box .dot{width:22px;height:22px;border-radius:50%;background:#e667a6;}
  .logo-box .name{font-size:48px;color:#e02fd6;letter-spacing:1px;}
  .headline{
    position:absolute;right:6px;top:30px;width:420px;margin:0;text-align:center;
    color:var(--white);font-weight:400;line-height:0.82;
    text-shadow:-5px 4px 0 rgba(74,31,99,.55);
  }
  .headline span{display:block;}
  .headline .a{font-size:150px;}
  .headline .girls{font-size:172px;letter-spacing:-2px;}
  .headline .only{font-size:166px;}
  .program{
    position:absolute;left:432px;top:418px;margin:0;font-size:49px;font-weight:400;
    color:var(--white);text-shadow:-3px 3px 0 rgba(74,31,99,.6);white-space:nowrap;
  }
  .program-note{position:absolute;right:37px;top:472px;margin:0;font-size:25px;color:var(--ink);}
  .brainchild{
    position:absolute;left:324px;top:548px;margin:0;font-size:42px;color:var(--pink-soft);
    text-shadow:-2px 2px 0 rgba(74,31,99,.5);white-space:nowrap;
  }
  .crew-title{
    position:absolute;left:400px;top:598px;width:364px;text-align:center;margin:0;
    font-size:52px;color:var(--pink-soft);text-shadow:-2px 2px 0 rgba(74,31,99,.55);
  }
  .panel{position:absolute;left:0;top:764px;width:861px;height:274px;background:var(--white);}
  .offer{position:absolute;left:118px;top:796px;}
  .offer h2,.about h2{margin:0;font-size:30px;font-weight:400;color:var(--ink);}
  .offer ul{list-style:none;margin:14px 0 0;padding:0;}
  .offer li{position:relative;font-size:22px;line-height:24px;margin-bottom:5px;color:var(--ink);}
  .offer li::before{
    content:"";position:absolute;left:-16px;top:7px;width:6px;height:6px;border-radius:50%;
    border:2px solid var(--ink);
  }
  .offer li.multi{line-height:22px;}
  .about{position:absolute;left:430px;top:790px;width:404px;}
  .about h2{text-align:center;font-size:26px;}
  .about p.story{
    margin:14px 0 0;font-family:"Oswald",sans-serif;font-weight:300;font-style:italic;
    font-size:13.4px;line-height:25.5px;text-transform:uppercase;letter-spacing:-.2px;
  }
  .hours{position:absolute;left:430px;top:970px;width:420px;text-align:center;}
  .hours .open{margin:0;font-family:"Oswald",sans-serif;font-weight:300;font-size:17px;text-transform:uppercase;}
  .hours .times{margin:12px 0 0;font-family:"Oswald",sans-serif;font-weight:600;font-size:16px;}
  .footer{position:absolute;left:0;top:1038px;width:861px;height:162px;background:var(--purple);}
  .contact{position:absolute;top:52px;color:var(--white);}
  .contact .label{display:flex;align-items:center;gap:6px;font-size:22px;color:var(--ink);}
  .contact .icon{width:34px;height:34px;}
  .contact .value{margin-top:6px;font-family:"Oswald",sans-serif;font-weight:600;font-size:14px;letter-spacing:-.3px;color:var(--white);white-space:nowrap;}
  .contact.phone .value{font-family:"Bebas Neue",sans-serif;font-weight:400;font-size:28px;margin-top:0;}
  .contact .note{font-size:8px;color:var(--white);margin-left:6px;}
  .contact.address{left:30px;}
  .contact.phone{left:220px;}
  .contact.email{left:396px;}
  .contact.fb{left:590px;}
</style>
</head>
<body>
<main class="flyer">
  <div class="desk-photo" role="img" aria-label="Soft photo of a white desk with a planner, binder rings and stationery"></div>

  <svg class="shapes" width="861" height="1200" viewBox="0 0 861 1200" aria-hidden="true">
    <polygon points="448,0 861,0 861,764 184,764" fill="var(--purple)"/>
  </svg>

  <div class="logo-box">
    <span class="dot"></span><span class="name">Ridge Lass Crew</span>
  </div>

  <h1 class="headline"><span class="a">A</span><span class="girls">Girls</span><span class="only">Only</span></h1>
  <p class="program">After School Program</p>
  <p class="program-note">As OSHC is no longer available</p>
  <p class="brainchild">The brainchild of Rebecca Folwin</p>
  <p class="crew-title">Ridge Lass Crew</p>

  <section class="panel"></section>

  <section class="offer">
    <h2>We Offer</h2>
    <ul>
      <li>Daily Meditation</li>
      <li>Healthy Snacks</li>
      <li>Dedicated Homework Time</li>
      <li class="multi">Organised Group Activity,<br>(Yoga, Fitness Class, Soccer etc.)</li>
      <li>Regular Guests Speakers</li>
      <li>Social Media Free Zone</li>
    </ul>
  </section>

  <section class="about">
    <h2>About Us</h2>
    <p class="story">The brainchild of Rebecca Folwin, Ridge Lass Crew was created to address the growing demand for after school/school holiday supervision for kids moving from primary into high school, when OSHC ceases to exist.</p>
  </section>

  <div class="hours">
    <p class="open">Open every afternoon and during school holidays</p>
    <p class="times">3-6pm Monday to Friday</p>
  </div>

  <footer class="footer">
    <div class="contact address">
      <div class="label">
        <svg class="icon" viewBox="0 0 34 34"><circle cx="17" cy="17" r="15" fill="none" stroke="#fff" stroke-width="2.5"/><path d="M17 8a6 6 0 0 0-6 6c0 5 6 11 6 11s6-6 6-11a6 6 0 0 0-6-6z" fill="#fff"/><circle cx="17" cy="14" r="2.2" fill="var(--purple)"/></svg>
        Address
      </div>
      <div class="value">87 Pelham Pde, Baulkham Hills</div>
      <div class="note">(ACROSS FROM CRESTMOOR DAY CLINIC)</div>
    </div>
    <div class="contact phone">
      <div class="label">
        <svg class="icon" viewBox="0 0 34 34"><circle cx="17" cy="17" r="15" fill="none" stroke="#fff" stroke-width="2.5"/><rect x="12" y="8" width="10" height="18" rx="2" fill="none" stroke="#fff" stroke-width="2"/><circle cx="17" cy="22.5" r="1" fill="#fff"/></svg>
        Phone
      </div>
      <div class="value">0455817396</div>
    </div>
    <div class="contact email">
      <div class="label">
        <svg class="icon" viewBox="0 0 34 34"><circle cx="17" cy="17" r="15" fill="none" stroke="#fff" stroke-width="2.5"/><rect x="9.5" y="11.5" width="15" height="11" rx="1.5" fill="none" stroke="#fff" stroke-width="2"/><path d="M10 12.5l7 5.5 7-5.5" fill="none" stroke="#fff" stroke-width="2"/></svg>
        Email
      </div>
      <div class="value">info@ridgelasscrew.example.au</div>
    </div>
    <div class="contact fb">
      <div class="label">
        <svg class="icon" viewBox="0 0 34 34"><circle cx="17" cy="17" r="15" fill="none" stroke="#fff" stroke-width="2.5"/></svg>
        FB Page
      </div>
      <div class="value">http://fb.example/ridgelasscrew</div>
    </div>
  </footer>
</main>
</body>
</html>
```